Business Card Design

We are a commercial real estate brokerage in San Francisco, leasing office buildings downtown.
I would like a clean, elegant look. Simple but powerful .

Industry/Entity Type

Business

Contact Information for Business Card

Derek Holloway
lic# 07258143
415.555.0172
derek@velt-commercial.example
velt-commercial.example

```html
<!DOCTYPE html>
<html lang="en">
<head>
<meta charset="utf-8">
<title>Velt Commercial – Business Card</title>
<link rel="stylesheet" href="https://fonts.googleapis.com/css2?family=Source+Sans+3:ital,wght@0,400;0,600;1,400&display=swap">
<style>
  :root {
    --page-bg: #e6e2dc;
    --card-bg: #eef0f2;
    --card-edge: #d5d9de;
    --ink: #2e333d;
    --brand: #3d4a66;
    --muted: #4c5260;
    --rule: #3a3f4a;
    --band: #4a5876;
    --band-ink: #e4e8f0;
    --mark: #8a909a;
  }
  * { margin: 0; padding: 0; box-sizing: border-box; }
  html, body { width: 1200px; height: 969px; overflow: hidden; }
  body {
    background: var(--page-bg);
    font-family: "Source Sans 3", Arial, sans-serif;
    color: var(--ink);
    position: relative;
  }
  .card {
    position: absolute;
    left: 100px; top: 201px;
    width: 1000px; height: 567px;
    background: var(--card-bg);
    border: 1px solid var(--card-edge);
    box-shadow: 0 10px 30px rgba(0,0,0,0.12);
  }
  .brand-mark {
    position: absolute;
    left: 92px; top: 118px;
    width: 96px; height: 96px;
    background: var(--mark);
  }
  .divider {
    position: absolute;
    left: 246px; top: 86px;
    width: 3px; height: 404px;
    background: var(--rule);
  }
  .brand-name {
    position: absolute;
    left: 266px; top: 88px;
    color: var(--brand);
    font-weight: 600;
    line-height: 1;
  }
  .brand-name .primary { display: block; font-size: 92px; letter-spacing: 1px; }
  .brand-name .secondary { display: block; font-size: 33px; letter-spacing: 1px; margin-top: 6px; }
  .icon {
    position: absolute;
    left: 186px;
    width: 26px; height: 26px;
    fill: var(--muted);
  }
  .agent-name {
    position: absolute;
    left: 268px; top: 253px;
    font-size: 36px; font-weight: 600;
    color: var(--brand);
  }
  .license, .contact {
    position: absolute;
    left: 268px;
    font-size: 26px;
    color: var(--ink);
  }
  .license { top: 302px; }
  .contact.phone { top: 362px; }
  .contact.email { top: 401px; }
  .contact.web { top: 440px; }
  .tagline-band {
    position: absolute;
    right: 0; top: 0;
    width: 200px; height: 100%;
    background: var(--band);
    display: flex; align-items: center; justify-content: center;
  }
  .tagline {
    writing-mode: vertical-rl;
    transform: rotate(180deg);
    text-align: center;
    font-style: italic;
    font-size: 27px;
    line-height: 38px;
    color: var(--band-ink);
  }
</style>
</head>
<body>
  <div class="card">
    <div class="brand-mark"></div>
    <div class="divider"></div>
    <div class="brand-name">
      <span class="primary">VELT</span>
      <span class="secondary">COMMERCIAL</span>
    </div>

    <svg class="icon" style="top:262px" viewBox="0 0 24 24" aria-hidden="true">
      <circle cx="12" cy="7" r="5"/><path d="M2 23c0-6 4.5-9 10-9s10 3 10 9z"/>
    </svg>
    <div class="agent-name">Derek Holloway</div>
    <div class="license">lic# 07258143</div>

    <svg class="icon" style="top:367px" viewBox="0 0 24 24" aria-hidden="true">
      <path d="M6.6 10.8a15 15 0 0 0 6.6 6.6l2.2-2.2a1 1 0 0 1 1-.25 11.4 11.4 0 0 0 3.6.57 1 1 0 0 1 1 1V20a1 1 0 0 1-1 1A17 17 0 0 1 3 4a1 1 0 0 1 1-1h3.5a1 1 0 0 1 1 1c0 1.25.2 2.45.57 3.57a1 1 0 0 1-.25 1z"/>
    </svg>
    <div class="contact phone">415.555.0172</div>

    <svg class="icon" style="top:407px" viewBox="0 0 24 24" aria-hidden="true">
      <path d="M2 5h20v14H2z M3.5 6.5 12 13l8.5-6.5" fill="none" stroke="var(--muted)" stroke-width="2"/>
      <path d="M2 5h20L12 12.5z"/>
    </svg>
    <div class="contact email">derek@velt-commercial.example</div>

    <svg class="icon" style="top:446px" viewBox="0 0 24 24" aria-hidden="true">
      <circle cx="12" cy="12" r="10"/>
      <path d="M2 12h20M12 2c3 3 3 17 0 20M12 2c-3 3-3 17 0 20" fill="none" stroke="var(--card-bg)" stroke-width="1.5"/>
    </svg>
    <div class="contact web">velt-commercial.example</div>

    <div class="tagline-band">
      <p class="tagline">commercial real estate<br>brokerage in San Francisco<br>leasing office buildings downtown.</p>
    </div>
  </div>
</body>
</html>
```